Sunset Harbor Living Web Page

We need a web page design that has two intro pages - first being a 'home page', then a link to the second page that has the 'content tabs' and a 'call to action' (see below).

The business helps people that wish to retire to S.E.Asia (Thailand, Malaysia, Indonesia,The Philippines etc) - to enjoy the lifestyle and the remaining years of their lives. What attracts S.E.Asia to many people is the lower cost, the atmoshpere and beauty of the tropics and the vibrancy of the various countries.

People that are wishing to make the most of their retirement and are adventurous at a great bargain compared to the cost of their own countries will be interested.

We help them achieve this - visa, financials (tax, gov't payments etc), introduce them to the right people for property, clubs, retirement facilities, insurance and so forth.

Therefore we are providing an extremely wide ranging service and this site will provide broad but general information only - with a call to action to come and see us for more specific information and how we can help them specifically.

This site will be predominantly for travel and lifestyle, it will be linked with another financial services (financial planning) site later down the track.

The colour scheme is dark green and blue - as per the attached logo design. Photos and background just think lifestyle and S.E.Asia - beaches/mountains/water/recreational activities for retirees.

Target market is mostly those coming up to retirement to those that are already retired. But we also expect to have some interest with younger people that would like to find out more and plan for the future. So a broad age group but I would say mostly 40-70 yrs old.

On the first (Home) page we would like our company name 'Sunset Harbor Living', our logo (which will be on all pages) and a statement such as: “Imagine a retirement where your dreams are brought to life, and you have never felt more alive. Let us show you how”. Then a link to the second page.

We would like an uncluttered site. On the second (contents) page the tabs would be:

- Visa
- Property
- Financials
- Travel
- Insurance & Healthcare
- Medical Tourism
- Cost of living
- Weekly Blogs and articles
- Sunset Harbor Living story

We would also like a call to action on the second page - asking them to leave their contact details if they wish to learn more or sign up to our weekly newsletter/blog.

We are open to suggestions and your imaginations.

Thank you
Malcolm

Font styles to use
Serif
Script

Colors
0255a3
3377b5
00a990
9bcb3c
abd036
33b8a4
85abd2
cadf82
86cfc6

Requirements
Must have
• I have been asked by the web designer to receive a 'Web Font' so that we can 'get off of Zentrofy'. Hope that makes sense.

```html
<!DOCTYPE html>
<html lang="en">
<head>
<meta charset="utf-8">
<title>Sunset Harbor Living</title>
<link rel="stylesheet" href="https://fonts.googleapis.com/css2?family=Cinzel:wght@400;700&family=Lato:wght@400;700;900&family=Roboto:wght@400;500;700&display=swap">
<style>
:root{
  --ink:#1d1d1d;
  --ink-soft:#2a2a2a;
  --blue:#1b9bd7;
  --green:#13a34c;
  --grey:#5b5b5b;
  --grey-light:#8a8a8a;
  --paper:#f4f4f4;
  --white:#ffffff;
}
*{box-sizing:border-box;margin:0;padding:0}
html,body{width:1200px;height:2711px;overflow:hidden}
body{position:relative;background:var(--white);font-family:"Lato",Arial,sans-serif;color:var(--grey)}
.abs{position:absolute}

/* header */
.site-header{left:0;top:0;width:1200px;height:100px;background:linear-gradient(#2b2b2b,#151515)}
.brand{left:87px;top:22px;display:flex;align-items:center;gap:12px}
.brand-dot{width:50px;height:50px;border-radius:50%;background:var(--green)}
.brand-name{font-family:"Roboto",Arial,sans-serif;font-weight:700;font-size:31px;color:var(--white);line-height:1;white-space:nowrap}
.social{display:flex;gap:10px}
.social span{width:28px;height:28px;border:2px solid var(--white);border-radius:50%;display:block}
.header-social{right:80px;top:17px}
.main-nav{right:80px;top:61px;display:flex;gap:31px;font-family:"Roboto",Arial,sans-serif;font-weight:700;font-size:14px;color:var(--white)}
.main-nav .active{position:relative}
.main-nav .active::after{content:"";position:absolute;left:-4px;right:-4px;top:28px;height:10px;background:var(--green)}

/* hero */
.hero{left:0;top:100px;width:1200px;height:583px;background:linear-gradient(180deg,#5b5d66 0%,#c79a62 30%,#e2b070 45%,#6e6a68 62%,#8d7258 80%,#a8875f 100%)}
.hero-title{left:0;top:372px;width:1200px;text-align:center;font-family:"Cinzel",Georgia,serif;font-weight:400;font-size:31px;line-height:41px;color:#fbf3e4;text-shadow:0 2px 4px rgba(0,0,0,.5)}
.hero-btn{left:434px;top:546px;width:334px;height:54px;background:var(--blue);border:2px solid var(--white);border-radius:4px;display:flex;align-items:center;padding-left:13px;font-family:"Roboto",Arial,sans-serif;font-weight:500;font-size:25px;color:var(--white)}
.go{position:absolute;right:0;top:0;border-radius:50%;background:var(--green);border:2px solid var(--white);display:flex;align-items:center;justify-content:center}
.hero-btn .go{right:-2px;top:-2px;width:54px;height:54px}
.slide-arrow{top:343px}

/* section heads */
.section-title{left:0;width:1200px;text-align:center;font-family:"Roboto",Arial,sans-serif;font-weight:500;font-size:36px}
.rule{left:380px;width:440px;height:14px}

/* welcome */
.welcome{left:0;top:683px;width:1200px;height:344px;background:var(--paper)}
.welcome-text{left:118px;top:822px;width:964px;text-align:center;font-size:13.5px;line-height:24px;color:#4a4a4a}
.pill-btn{height:36px;border-radius:4px;display:flex;align-items:center;justify-content:center;font-family:"Roboto",Arial,sans-serif;font-weight:700;font-size:15px;color:var(--white);letter-spacing:.3px}
.read-more{left:526px;top:940px;width:148px;background:var(--blue);justify-content:flex-start;padding-left:14px}
.pill-btn .go{width:36px;height:36px}

/* services */
.services{left:0;top:1027px;width:1200px;height:451px;background:var(--blue)}
.service-card{top:1166px;width:239px;height:159px;border:4px solid var(--white);box-shadow:0 2px 6px rgba(0,0,0,.3)}
.service-label{top:1340px;width:239px;text-align:center;font-family:"Roboto",Arial,sans-serif;font-weight:500;font-size:19px;color:var(--white);letter-spacing:.5px}
.view-all{left:492px;top:1397px;width:215px;height:38px;background:var(--green)}

/* news & testimonials */
.block-title{top:1527px;font-family:"Roboto",Arial,sans-serif;font-size:35px;color:#5a5a5a;font-weight:500}
.block-title b{color:var(--ink);font-weight:700}
.block-line{height:1px;background:#d4d4d4}
.news-item{left:81px;width:490px;height:100px}
.news-thumb{left:0;top:0;width:101px;height:101px;border:3px solid var(--white);box-shadow:0 1px 4px rgba(0,0,0,.35)}
.news-body{left:123px;top:0;width:370px}
.news-body h3{font-family:"Roboto",Arial,sans-serif;font-weight:500;font-size:16px;color:var(--ink);margin-bottom:4px}
.news-date{font-size:11.5px;font-style:italic;color:var(--grey-light);margin-bottom:3px}
.news-body p{font-size:12px;line-height:18px;color:#555}
.news-more{font-size:11px;font-weight:900;color:var(--green);margin-top:2px}
.col-divider{left:609px;top:1527px;width:2px;height:358px;background:#bdbdbd}
.avatar{left:650px;top:1604px;width:88px;height:88px;border-radius:50%;border:4px solid var(--blue);background:linear-gradient(#d9d9d9,#9fa6ad)}
.client-name{left:760px;top:1630px;font-family:"Roboto",Arial,sans-serif;font-weight:700;font-size:17px;color:var(--ink)}
.client-role{left:760px;top:1654px;font-size:13px;font-weight:700;color:var(--green)}
.quote{left:650px;top:1708px;width:470px;font-style:italic;font-size:13.5px;line-height:27px;color:#4a4a4a}
.quote .mark{font-family:Georgia,serif;font-style:normal;font-weight:700;font-size:34px;color:var(--ink-soft);line-height:0;vertical-align:-12px}

/* contact */
.contact{left:0;top:1928px;width:1200px;height:484px;background:linear-gradient(180deg,#3d4a52 0%,#4d5e66 40%,#2e3a41 75%,#222a2e 100%)}
.field{height:38px;background:var(--white);font-size:12px;color:#6a6a6a;padding:12px 10px}
.submit{left:535px;top:2206px;width:130px;background:var(--blue);justify-content:flex-start;padding-left:22px}

/* footer */
.footer{left:0;top:2412px;width:1200px;height:248px;background:var(--ink)}
.map{left:81px;top:2430px;width:262px;height:185px;border:3px solid var(--white);background:linear-gradient(135deg,#e6e2d6,#cfd9c6 55%,#b8d0e2)}
.foot-title{font-family:"Roboto",Arial,sans-serif;font-weight:700;font-size:14px;color:var(--white)}
.foot-text{font-size:13px;line-height:22px;color:#b5b5b5}
.contact-row{display:flex;align-items:center;gap:10px}
.contact-row small{display:block;font-size:11px;color:#b5b5b5}
.contact-row strong{display:block;font-size:14px;font-weight:400;color:var(--white);white-space:nowrap}
.ring{width:26px;height:26px;border-radius:50%;border:2px solid var(--green);display:flex;align-items:center;justify-content:center;flex:none}
.news-head{left:598px;top:2459px;display:flex;align-items:center;gap:10px;font-family:"Roboto",Arial,sans-serif;font-weight:700;font-size:19px;color:var(--white)}
.signup-field{left:598px;top:2526px;width:239px;height:36px;border:1px solid #777;background:#1c1c1c;color:var(--white);font-size:12px;padding:10px}
.signup-btn{left:598px;top:2580px;width:123px;height:36px;background:var(--green)}
.foot-brand{left:840px;top:2468px;width:320px;text-align:center}
.foot-brand .brand-dot{width:84px;height:84px;margin:0 auto 12px}
.foot-brand .brand-name{font-size:28px}
.copy-bar{left:0;top:2660px;width:1200px;height:51px;background:var(--green)}
.copy{left:81px;top:2678px;font-size:13px;font-weight:700;color:var(--white)}
.foot-social{right:81px;top:2669px}
.foot-social span{width:30px;height:30px}
</style>
</head>
<body>

<header class="site-header abs"></header>
<div class="brand abs"><span class="brand-dot"></span><span class="brand-name">Sunset Harbor Living</span></div>
<div class="social header-social abs"><span></span><span></span><span></span><span></span></div>
<nav class="main-nav abs">
  <span class="active">HOME</span><span>SERVICES</span><span>BLOG &amp; ARTICLES</span><span>OUR STORY</span><span>CONTACT US</span>
</nav>

<section class="hero abs" role="img" aria-label="Retired couple in beach chairs watching the sunset over the sea"></section>
<svg class="slide-arrow abs" style="left:40px" width="44" height="74" viewBox="0 0 44 74"><polyline points="40,4 6,37 40,70" fill="none" stroke="#fff" stroke-width="4"/></svg>
<svg class="slide-arrow abs" style="right:40px" width="44" height="74" viewBox="0 0 44 74"><polyline points="4,4 38,37 4,70" fill="none" stroke="#fff" stroke-width="4"/></svg>
<h1 class="hero-title abs">Imagine A Retirement Where Your Dreams Are<br>Brought To Life,<br>&amp; You Have Never Felt More Alive</h1>
<a class="hero-btn abs">Let Us Show You How
  <span class="go"><svg width="26" height="20" viewBox="0 0 26 20"><polyline points="3,2 11,10 3,18" fill="none" stroke="#fff" stroke-width="3"/><polyline points="13,2 21,10 13,18" fill="none" stroke="#fff" stroke-width="3"/></svg></span>
</a>

<section class="welcome abs"></section>
<h2 class="section-title abs" style="top:732px;color:#5a5a5a">Welcome To <b style="color:var(--blue);font-weight:500">Sunset Harbor Living</b></h2>
<svg class="rule abs" style="top:786px" viewBox="0 0 440 14"><line x1="0" y1="7" x2="440" y2="7" stroke="#cfcfcf"/><circle cx="220" cy="7" r="6" fill="var(--green)"/></svg>
<p class="welcome-text abs">Lorem ipsum dolor sit amet, consectetuer adipiscing elit, sed diam nonummy nibh euismod tincidunt ut laoreet dolore magna aliquam erat volutpat. Ut wisi enim ad minim veniam, quis nostrud exerci tation ullamcorper suscipit lobortis nisl ut aliquip ex ea commodo consequat. Duis autem vel eum iriure dolor in hendrerit in vulputate velit esse molestie consequat, vel illum dolore eu feugiat nulla facilisis at vero eros et accumsan et iusto odio dignissim qui blandit praesent luptatum zzril delenit augue duis dolore te feugait nulla facilisi.</p>
<a class="pill-btn read-more abs">READ MORE<span class="go"><svg width="18" height="14" viewBox="0 0 18 14"><polyline points="2,1 7,7 2,13" fill="none" stroke="#fff" stroke-width="2"/><polyline points="9,1 14,7 9,13" fill="none" stroke="#fff" stroke-width="2"/></svg></span></a>

<section class="services abs"></section>
<h2 class="section-title abs" style="top:1067px;color:var(--white)">Our Services</h2>
<svg class="rule abs" style="top:1120px" viewBox="0 0 440 14"><line x1="0" y1="7" x2="440" y2="7" stroke="#6cc0e8"/><circle cx="220" cy="7" r="6" fill="#0f7fb4"/></svg>
<svg class="abs" style="left:38px;top:1230px" width="20" height="32" viewBox="0 0 20 32"><polyline points="17,2 3,16 17,30" fill="none" stroke="#fff" stroke-width="2.5"/></svg>
<svg class="abs" style="right:38px;top:1230px" width="20" height="32" viewBox="0 0 20 32"><polyline points="3,2 17,16 3,30" fill="none" stroke="#fff" stroke-width="2.5"/></svg>
<div class="service-card abs" style="left:81px;background:linear-gradient(135deg,#c9a98a,#7d5a43)" role="img" aria-label="Passport and visa stamps"></div>
<div class="service-card abs" style="left:347px;background:linear-gradient(135deg,#8fbf4f,#3e6b22)" role="img" aria-label="Model house held in an open hand"></div>
<div class="service-card abs" style="left:614px;background:linear-gradient(135deg,#dfe6ef,#6f8bb2)" role="img" aria-label="Financial statements with a calculator and pen"></div>
<div class="service-card abs" style="left:880px;background:linear-gradient(135deg,#b9cde4,#eef2f7 55%,#7b8ea6)" role="img" aria-label="Traveller resting on a snowy mountain"></div>
<div class="service-label abs" style="left:81px">VISA</div>
<div class="service-label abs" style="left:347px">PROPERTY</div>
<div class="service-label abs" style="left:614px">FINANCIALS</div>
<div class="service-label abs" style="left:880px">TRAVEL</div>
<a class="pill-btn view-all abs">VIEW ALL SERVICE</a>

<h2 class="block-title abs" style="left:81px">Latest <b>News</b></h2>
<svg class="abs" style="left:527px;top:1538px" width="44" height="24" viewBox="0 0 44 24"><polyline points="14,2 4,12 14,22" fill="none" stroke="#aaa" stroke-width="2"/><polyline points="30,2 40,12 30,22" fill="none" stroke="#222" stroke-width="2"/></svg>
<div class="block-line abs" style="left:81px;top:1584px;width:490px"></div>
<article class="news-item abs" style="top:1624px">
  <div class="news-thumb abs" style="background:linear-gradient(160deg,#4ea1d8,#86c0a1 55%,#e8dcc0)" role="img" aria-label="Tropical beach with palm trees"></div>
  <div class="news-body abs">
    <h3>Ut tellus dolor, dapibus smit dollar nomk egemop</h3>
    <div class="news-date">Posted On 01.01.2015</div>
    <p>Duis autem vel eum iriure dolor in hendrerit in at vero erosacc sa iusto odio dignissim quosli blandit praesent luptatum zzrilini douis</p>
    <div class="news-more">READ MORE</div>
  </div>
</article>
<div class="block-line abs" style="left:81px;top:1748px;width:490px"></div>
<article class="news-item abs" style="top:1771px">
  <div class="news-thumb abs" style="background:linear-gradient(160deg,#e9c07a,#b47a4a 60%,#6d4b33)" role="img" aria-label="Family walking on the beach at sunset"></div>
  <div class="news-body abs">
    <h3>Ut tellus dolor, dapibus smit dollar nomk egemop</h3>
    <div class="news-date">Posted On 01.01.2015</div>
    <p>Duis autem vel eum iriure dolor in hendrerit in at vero erosacc sa iusto odio dignissim quosli blandit praesent luptatum zzrilini douis</p>
    <div class="news-more">READ MORE</div>
  </div>
</article>

<div class="col-divider abs"></div>

<h2 class="block-title abs" style="left:651px">Client <b>Testimonials</b></h2>
<svg class="abs" style="left:1076px;top:1538px" width="44" height="24" viewBox="0 0 44 24"><polyline points="14,2 4,12 14,22" fill="none" stroke="#aaa" stroke-width="2"/><polyline points="30,2 40,12 30,22" fill="none" stroke="#222" stroke-width="2"/></svg>
<div class="block-line abs" style="left:651px;top:1584px;width:469px"></div>
<div class="avatar abs" role="img" aria-label="Client portrait"></div>
<div class="client-name abs">MR. QUIS NOSTRUD EXERCI</div>
<div class="client-role abs">Business Man</div>
<p class="quote abs"><span class="mark">“</span> Utm tellus dolor, dapibus eget, elemen velmki cursus eleifelita arnanokmn auctorbni wisi et urnam. Lorem ipsum dolor sit amet, conse ctetur adipisc ngop elit. Nulla in sollic itudin velit, bibendum velit.Cras vel facilisis ipsum,et venenat risus. Duis autem vel eum iriure dolor in hendrerit in at vero erosacc sa iustoml odio dignissim quosliin sollic itudin <span class="mark">”</span></p>

<section class="contact abs" role="img" aria-label="Palm fronds over a calm tropical sea at dusk"></section>
<h2 class="section-title abs" style="top:1984px;color:var(--white)">Get In Touch</h2>
<svg class="rule abs" style="top:2038px" viewBox="0 0 440 14"><line x1="0" y1="7" x2="440" y2="7" stroke="#8a959b"/><circle cx="220" cy="7" r="6" fill="#9aa4aa"/></svg>
<div class="field abs" style="left:210px;top:2091px;width:249px">Enter Your Name</div>
<div class="field abs" style="left:475px;top:2091px;width:250px">Enter Your Email Address</div>
<div class="field abs" style="left:743px;top:2091px;width:247px">Enter Your Phone Number</div>
<div class="field abs" style="left:210px;top:2149px;width:249px">Enter Your Location</div>
<div class="field abs" style="left:475px;top:2149px;width:515px">Enter Your Comments</div>
<a class="pill-btn submit abs">SUBMIT<span class="go"><svg width="18" height="14" viewBox="0 0 18 14"><polyline points="2,1 7,7 2,13" fill="none" stroke="#fff" stroke-width="2"/><polyline points="9,1 14,7 9,13" fill="none" stroke="#fff" stroke-width="2"/></svg></span></a>

<footer class="footer abs"></footer>
<div class="map abs" role="img" aria-label="Street map with office location pin"></div>
<div class="abs" style="left:367px;top:2431px;width:210px">
  <div class="foot-title">SUNSET HARBOR LIVING</div>
  <div class="foot-text">Duis autem vel eum iriure<br>dolor in hendrerit in at vero</div>
  <div class="contact-row" style="margin-top:12px">
    <span class="ring"><svg width="12" height="12" viewBox="0 0 12 12"><path d="M2 1 L4.5 1 L5.5 4 L4 5 C5 7 6 8 7 8.5 L8 7 L11 8 L11 10.5 C6 11 1 6 2 1Z" fill="var(--green)"/></svg></span>
    <span><small>Call Us Today</small><strong>(555) 014-2290</strong></span>
  </div>
  <div class="contact-row" style="margin-top:12px">
    <span class="ring"><svg width="12" height="10" viewBox="0 0 12 10"><rect x="1" y="1" width="10" height="8" fill="none" stroke="var(--green)" stroke-width="1.5"/><polyline points="1,1 6,5.5 11,1" fill="none" stroke="var(--green)" stroke-width="1.5"/></svg></span>
    <span><small>Write To Us</small><strong>info@sunsetharborliving.com</strong></span>
  </div>
</div>
<div class="news-head abs"><svg width="30" height="20" viewBox="0 0 30 20"><polygon points="0,0 30,4 10,20 12,8" fill="var(--green)"/></svg>Newsletter Signup</div>
<div class="foot-text abs" style="left:598px;top:2496px;font-size:12px">Sign Up To Our Weekly Newsletter/ Blog!</div>
<div class="signup-field abs">Enter Your Email Here</div>
<a class="pill-btn signup-btn abs">SIGNUP</a>
<div class="foot-brand abs"><div class="brand-dot"></div><div class="brand-name">Sunset Harbor Living</div></div>

<div class="copy-bar abs"></div>
<div class="copy abs">Copyright © 2016 Sunset Harbor Living &nbsp;|&nbsp; All Rights Reserved.</div>
<div class="social foot-social abs"><span></span><span></span><span></span><span></span></div>

</body>
</html>
```